business card design for a plumbing contractor

i need a double business card for a plumbing business, our initial service is residential Sewer Drain Cleaning.

Target Market(s)

other plumbing Business

Industry/Entity Type

Plumbing

Contact Information for Business Card

www.PipeworksTopMark.example- 5307218394-

Font styles to use
Serif

Colors
ec1f27
0455a3

```html
<!DOCTYPE html>
<html lang="en">
<head>
<meta charset="utf-8">
<title>Pipeworks TopMark – Business Card</title>
<link rel="stylesheet" href="https://fonts.googleapis.com/css2?family=Arimo:wght@400;700&display=swap">
<style>
  :root {
    --brand-blue: #0455a3;
    --brand-blue-deep: #0a4a8c;
    --brand-red: #ec1f27;
    --brand-red-deep: #c8161d;
    --ink-warm: #6f665a;
    --paper: #ffffff;
    --paper-shade: #eeeeee;
    --stage: #e4e6ea;
    --text-dark: #1a1a1a;
  }
  * { box-sizing: border-box; margin: 0; padding: 0; }
  html, body {
    width: 1200px; height: 997px; overflow: hidden;
    background: var(--stage);
    font-family: "Arimo", Arial, sans-serif;
  }
  .sheet {
    width: 1200px; height: 997px;
    display: flex; flex-direction: column; align-items: center; justify-content: center;
    gap: 70px;
  }
  .card {
    width: 640px; height: 366px;
    border-radius: 26px;
    position: relative; overflow: hidden;
    box-shadow: 0 10px 28px rgba(0,0,0,0.18);
  }

  /* Card back */
  .card-back {
    background: radial-gradient(ellipse at 50% 40%, #0c5fae 0%, var(--brand-blue) 55%, var(--brand-blue-deep) 100%);
    display: flex; align-items: center; justify-content: center;
  }
  .wordmark {
    display: flex; align-items: center; gap: 16px;
    font-weight: 700; font-size: 46px; letter-spacing: 0.5px;
  }
  .card-back .wordmark { color: var(--paper); }
  .wordmark-dot {
    width: 34px; height: 34px; border-radius: 50%;
    background: var(--brand-red); flex: none;
  }

  /* Card front */
  .card-front {
    background: linear-gradient(180deg, var(--paper) 0%, var(--paper) 60%, var(--paper-shade) 100%);
  }
  .card-front .wordmark {
    position: absolute; top: 70px; left: 0; right: 0;
    justify-content: center;
    color: var(--ink-warm); font-size: 44px;
  }
  .rule {
    position: absolute; height: 2px;
  }
  .rule-red-top { left: 0; width: 330px; top: 200px; background: var(--brand-red); }
  .rule-red-top2 { left: 0; width: 330px; top: 206px; height: 1px; background: var(--brand-red); }
  .rule-blue-top { left: 330px; right: 0; top: 178px; background: var(--brand-blue); }
  .rule-red-bottom { left: 0; width: 330px; top: 320px; height: 1px; background: var(--brand-red); }

  .name-panel {
    position: absolute; left: 0; top: 212px; width: 330px; height: 102px;
    background: linear-gradient(180deg, var(--brand-red) 0%, var(--brand-red-deep) 100%);
    padding: 36px 0 0 96px;
  }
  .person-name {
    color: var(--paper); font-weight: 700; font-size: 19px; letter-spacing: 0.6px;
  }
  .person-role {
    color: var(--text-dark); font-weight: 700; font-size: 15px; margin: 2px 0 0 42px;
  }

  .contact-panel {
    position: absolute; left: 330px; right: 0; top: 184px; height: 130px;
    background: var(--brand-blue);
    padding: 22px 0 0 30px;
    list-style: none;
  }
  .contact-item {
    display: flex; align-items: center; gap: 10px;
    color: var(--paper); font-size: 13px; height: 26px;
  }
  .contact-icon { width: 16px; height: 16px; flex: none; }

  .services {
    position: absolute; left: 0; right: 0; top: 332px;
    text-align: center; font-size: 13px; letter-spacing: 0.5px;
    color: var(--brand-blue); text-transform: uppercase;
  }
  .services .accent { color: var(--brand-red); }
</style>
</head>
<body>
<main class="sheet">

  <section class="card card-back" aria-label="Card back">
    <div class="wordmark"><span>Pipeworks TopMark</span><span class="wordmark-dot" aria-hidden="true"></span></div>
  </section>

  <section class="card card-front" aria-label="Card front">
    <div class="wordmark"><span>Pipeworks TopMark</span><span class="wordmark-dot" aria-hidden="true"></span></div>

    <div class="rule rule-red-top"></div>
    <div class="rule rule-red-top2"></div>
    <div class="rule rule-blue-top"></div>

    <div class="name-panel">
      <p class="person-name">MARTIN HALE</p>
      <p class="person-role">Director</p>
    </div>

    <ul class="contact-panel">
      <li class="contact-item">
        <svg class="contact-icon" viewBox="0 0 16 16" aria-hidden="true">
          <circle cx="8" cy="8" r="8" fill="#fff"/>
          <path d="M5.2 4.2l1.6-.2.8 2-1 .8c.5 1.1 1.4 2 2.5 2.5l.8-1 2 .8-.2 1.6c-3.6.3-6.8-2.9-6.5-6.5z" fill="#0455a3"/>
        </svg>
        <span>5307218394</span>
      </li>
      <li class="contact-item">
        <svg class="contact-icon" viewBox="0 0 16 16" aria-hidden="true">
          <circle cx="8" cy="8" r="8" fill="#fff"/>
          <rect x="4" y="5.2" width="8" height="5.6" rx="0.6" fill="none" stroke="#0455a3" stroke-width="1.1"/>
          <path d="M4.2 5.6L8 8.5l3.8-2.9" fill="none" stroke="#0455a3" stroke-width="1.1"/>
        </svg>
        <span>dispatch@PipeworksTopMark.example</span>
      </li>
      <li class="contact-item">
        <svg class="contact-icon" viewBox="0 0 16 16" aria-hidden="true">
          <circle cx="8" cy="8" r="8" fill="#fff"/>
          <circle cx="8" cy="8" r="4" fill="none" stroke="#0455a3" stroke-width="1"/>
          <ellipse cx="8" cy="8" rx="1.7" ry="4" fill="none" stroke="#0455a3" stroke-width="0.9"/>
          <path d="M4 8h8" stroke="#0455a3" stroke-width="0.9"/>
        </svg>
        <span>www.PipeworksTopMark.example</span>
      </li>
    </ul>

    <div class="rule rule-red-bottom"></div>

    <p class="services">Sewer Drain Cleaning, <span class="accent">Maintenance,</span> Trenchless Pipe Installs</p>
  </section>

</main>
</body>
</html>
```